Flyer für Verkauf von Radondetektoren
Zielgruppe
Ich verkaufe Radondetektoren zur Messung von Radon in Innenräumen. Zielgruppe sind Privatpersonen, Firmen, Genossenschaften und andere Hauseigentümer.
Aufgabenstellung
Ich brauche das Design für meine Messanleitung.
Kreativ - modern - weniger kann mehr sein
Struktur ist wichtigt, es soll also einfach sein zu lesen und zu verstehen, was gemacht werden soll. Können Bulletpoints, Icons mit eingebracht werden.
Wichtig ist auch, dass die beiden Logos 'Luftprüfer.de' und TESTOVAL' auf der Messanleitung vorhanden sind. Wobei 'Luftprüfer.de' das Hauptlogo ist.
DIN format dachte ich A4 beidseitig (Text müsste also auf diese Grösse angepasst werden).
Kann natürlich auch Flyer-Format sein oder andere Vorschläge!
Bildmaterial gibt es auf unsere Homepage https://luftprüfer.de und https://luftkontroll.se . Diese haben wir bereits gekauft und können verwendet werden. Ich lade sie den bei Bedarf hoch. Es können natürlich auch andere Vorschläge kommen.

```html
<!DOCTYPE html>
<html lang="de">
<head>
<meta charset="utf-8">
<title>Messanleitung – Luftprüfer.de</title>
<link href="https://fonts.googleapis.com/css2?family=Roboto:wght@400;500;700;900&family=Roboto+Condensed:ital,wght@0,400;0,700;1,400;1,700&display=swap" rel="stylesheet">
<style>
:root{
  --yellow:#f4b71c;
  --yellow-light:#f9d66b;
  --orange:#e8911a;
  --ink:#2f2f2f;
  --text:#3a3a3a;
  --grey:#e4e4e4;
  --white:#ffffff;
  --partner:#3b4d7c;
  --bg:#d9d4cf;
}
*{box-sizing:border-box;margin:0;padding:0}
html,body{width:1200px;height:1195px;overflow:hidden;background:var(--bg)}
body{font-family:"Roboto Condensed",Arial,sans-serif;color:var(--text)}
.sheet{position:absolute;left:150px;width:900px;height:582px;display:flex;box-shadow:0 2px 8px rgba(0,0,0,.18)}
.sheet--outside{top:8px}
.sheet--inside{top:604px}
.panel{position:relative;width:300px;height:582px;overflow:hidden;background:var(--white);padding:0 18px}
.panel--grey{background:linear-gradient(180deg,#ececec,#dcdcdc)}
.panel--soft{background:linear-gradient(180deg,#f3f3f3,#e6e6e6)}
p,li{font-size:8px;line-height:1.42}
.justify{text-align:justify}
.bullets{list-style:none;margin-top:3px}
.bullets li{padding-left:11px;position:relative;margin-bottom:2px;text-align:justify}
.bullets li::before{content:"»";position:absolute;left:0;top:-1px;font-weight:700;font-size:9px;color:var(--ink)}
.step{position:relative;height:44px;margin:14px -18px 0 -18px;padding-left:18px;display:flex;align-items:center;
  background:repeating-linear-gradient(-55deg,rgba(255,255,255,.25) 0 1px,transparent 1px 5px),linear-gradient(90deg,var(--yellow-light),var(--yellow) 75%,rgba(244,183,28,0) 100%);}
.step__num{font-family:Roboto,sans-serif;font-weight:700;font-size:19px;color:var(--ink)}
.step__label{font-family:Roboto,sans-serif;font-size:12px;letter-spacing:.5px;color:var(--ink);margin-left:4px;margin-top:3px}
.step__icon{position:absolute;right:14px;top:4px;width:36px;height:36px;border-radius:50%;background:var(--yellow);border:2px solid var(--white);display:flex;align-items:center;justify-content:center}
.heading{font-family:Roboto,sans-serif;font-weight:700;font-size:17px;line-height:1.18;color:var(--ink);letter-spacing:.3px;margin:22px 0 10px}
.sub{display:flex;align-items:center;gap:8px;margin:14px 0 4px}
.sub h3{font-family:Roboto,sans-serif;font-weight:700;font-size:9.5px;color:var(--ink)}
.note{display:flex;gap:8px;align-items:center;margin:12px 0}
.note p{font-style:italic;font-weight:700;font-size:9px}
.small-h{font-style:italic;font-weight:700;margin-top:10px}
.url{display:inline-block;background:var(--yellow);border:1.5px solid var(--ink);border-radius:12px;padding:4px 12px;font-family:Roboto,sans-serif;font-weight:700;font-size:9px;color:var(--ink);margin:10px 0 12px 10px}
.address{display:flex;gap:10px;align-items:flex-start;margin:12px 0}
.partner{position:absolute;left:18px;bottom:26px;display:flex;align-items:center;gap:7px}
.partner__dot{width:14px;height:14px;border-radius:50%;background:var(--partner)}
.partner__name{font-family:Roboto,sans-serif;font-weight:500;font-size:20px;color:var(--partner);letter-spacing:.5px}
.cover{padding:0;background:var(--grey)}
.cover__band{height:28px;background:var(--yellow)}
.cover__title{position:relative;background:var(--white);margin-top:22px;height:132px;padding:18px 14px 0 32px}
.cover__title::before{content:"";position:absolute;left:0;top:0;width:16px;height:100%;background:var(--orange)}
.cover__title h1{font-family:Roboto,sans-serif;font-weight:700;font-size:26px;color:var(--ink);letter-spacing:.4px}
.cover__title p{font-family:Roboto,sans-serif;font-size:12.6px;line-height:1.45;color:var(--ink);margin-top:6px}
.cover__art{height:320px;background:radial-gradient(circle at 60% 20%,#fbd968,var(--yellow) 45%,#d7951c 80%,#a86a1a)}
.brand{position:absolute;left:24px;bottom:30px;display:flex;align-items:center;gap:9px}
.brand__dot{width:22px;height:22px;border-radius:50%;background:var(--yellow)}
.brand__name{font-family:Roboto,sans-serif;font-size:23px;color:var(--ink)}
.brand__tag{position:absolute;left:55px;bottom:15px;font-family:Roboto,sans-serif;font-size:9px;letter-spacing:.6px;color:var(--orange)}
.strip-art{height:70px;margin:0 -18px;background:linear-gradient(90deg,var(--yellow),#f9d66b 40%,#e6a22a 80%,var(--yellow))}
</style>
</head>
<body>

<section class="sheet sheet--outside">
  <article class="panel">
    <div class="step">
      <span class="step__num">3.</span><span class="step__label">SCHRITT</span>
      <span class="step__icon"><svg width="20" height="20" viewBox="0 0 20 20"><circle cx="10" cy="11" r="7" fill="none" stroke="#2f2f2f" stroke-width="1.6"/><path d="M10 11V4L15 9Z" fill="#2f2f2f"/></svg></span>
    </div>
    <h2 class="heading">RADONMESSUNG</h2>
    <p>Die Radonmessung beginnt, sobald Sie die radondichten Verpackungen öffnen.</p>
    <div class="note">
      <svg width="26" height="26" viewBox="0 0 26 26"><rect x="2" y="6" width="17" height="17" rx="3" fill="none" stroke="#2f2f2f" stroke-width="2"/><path d="M6 14l5 5 12-15" fill="none" stroke="#f4b71c" stroke-width="3"/></svg>
      <p>Bitte halten Sie die Messdauer wie folgt ein:</p>
    </div>
    <div class="sub">
      <svg width="22" height="22" viewBox="0 0 22 22"><circle cx="11" cy="11" r="9" fill="none" stroke="#f4b71c" stroke-width="1.6"/><path d="M11 5v6l4 3" fill="none" stroke="#f4b71c" stroke-width="1.6"/></svg>
      <h3>Kurzzeitmessung</h3>
    </div>
    <ul class="bullets">
      <li>Mindestmessdauer 10 Tage (bis hin zu 30 Tagen).</li>
      <li>Führen Sie die Messung vorzugsweise in der Heizperiode (1. Oktober – 30. April) durch.</li>
      <li>Kurzzeitmessungen werden oft beim Kauf oder Verkauf von Immobilien genutzt, um ein mögliches Gefährdungspotential abschätzen zu können, oder wenn die Zeit nicht ausreicht, um eine Langzeitmessung durchzuführen.</li>
    </ul>
    <div class="sub">
      <svg width="22" height="22" viewBox="0 0 22 22"><circle cx="11" cy="11" r="9" fill="none" stroke="#f4b71c" stroke-width="1.6"/><path d="M11 5v6l4 3" fill="none" stroke="#f4b71c" stroke-width="1.6"/></svg>
      <h3>Langzeitmessung</h3>
    </div>
    <ul class="bullets">
      <li>Mindestmessdauer 3 Monate während der Heizperiode (1. Oktober – 30. April).</li>
      <li>Um einen Jahresmittelwert der Radonkonzentration in Innenräumen ermitteln zu können, halten Sie die Messdauer von 12 Monaten ein.</li>
      <li>Falls Ihr Arbeitsplatz in einem Radon-Vorsorgegebiet liegt und somit der Messpflicht unterliegt, muss die Messdauer von 12 Monaten eingehalten werden.</li>
    </ul>
  </article>

  <article class="panel">
    <div class="step">
      <span class="step__num">4.</span><span class="step__label">SCHRITT</span>
      <span class="step__icon"><svg width="20" height="20" viewBox="0 0 20 20"><path d="M3 17h14" stroke="#2f2f2f" stroke-width="1.6"/><rect x="4" y="10" width="2.5" height="6" fill="#2f2f2f"/><rect x="8" y="7" width="2.5" height="9" fill="#2f2f2f"/><rect x="12" y="4" width="2.5" height="12" fill="#2f2f2f"/></svg></span>
    </div>
    <h2 class="heading" style="margin-top:14px">AUSWERTUNG<br>UND PRÜFBERICHT</h2>
    <p class="justify">Nach Ablauf der Messdauer, loggen Sie sich wieder auf <b>https://kundenportal.testoval.se/de</b> in Ihrem Account ein. Vermerken Sie hier das Ende der Messung und senden Sie anschließend alle Radondetektoren ausreichend frankiert in einem Umschlag oder einem Karton zeitnah an unsere Rücksendeadresse:</p>
    <div class="address">
      <svg width="26" height="18" viewBox="0 0 26 18"><rect x="1" y="1" width="24" height="16" fill="none" stroke="#e8911a" stroke-width="1.5"/><path d="M1 1l12 9 12-9" fill="none" stroke="#e8911a" stroke-width="1.5"/></svg>
      <p><b>Luftprüfer.de</b><br>Lindenallee 14, 28195 Bremen</p>
    </div>
    <p class="justify">Sobald die Radondetektoren im Labor von TESTOVAL eingetroffen sind, werden diese fachgerecht analysiert und die Ergebnisse der Radonmessung ausgewertet. Ein vollständiger Prüfbericht wird Ihnen innerhalb 36 Stunden nach Erhalt der Detektoren im Labor per E-Mail zugeschickt.</p>
    <p class="small-h">Weitere Hinweise</p>
    <p>• Bitte beachten Sie, dass die Radonmessung innerhalb von 15 Monaten nach Kaufdatum abgeschlossen sein muss.<br>
    • Versuchen Sie nicht das Gehäuse der Detektoren zu öffnen und platzieren Sie diese immer außer Reichweite von Kindern.<br>
    • Während der gesamten Messdauer dürfen die Detektoren nicht an einem anderen Ort umplatziert werden.<br>
    • Durch die Anmeldung auf der Website https://kundenportal.testoval.se/de und die Eingabe der erforderlichen Daten bestätigt der/die Wohnungseigentümer*in/Messverantwortliche, dass er/sie die Messanleitung befolgt hat und die Detektoren gemäß den Anweisungen korrekt platziert wurden.</p>
    <p class="small-h">Datenschutz (GDPR), Impressum und AGBs</p>
    <p>Mehr Information dazu finden Sie unter www.luftprüfer.de<br>Copyright © 2023 Nordluft Mätteknik AB<br>Alle Rechte vorbehalten www.luftprüfer.de</p>
    <div class="partner"><span class="partner__dot"></span><span class="partner__name">TESTOVAL</span></div>
  </article>

  <article class="panel cover">
    <div class="cover__band"></div>
    <div class="cover__title">
      <h1>MESSANLEITUNG</h1>
      <p>für Radonmessungen<br>von Innenraumluft<br>mit passiven Radon Detektoren</p>
    </div>
    <div class="cover__art" role="img" aria-label="Illustration: Stadtsilhouette mit Häusern, Hochhäusern und Bäumen in Gelb- und Brauntönen vor Sonnenstrahlen"></div>
    <div class="brand"><span class="brand__dot"></span><span class="brand__name">Luftprüfer.de</span></div>
    <span class="brand__tag">LUFTQUALITÄT EINFACH GEPRÜFT</span>
  </article>
</section>

<section class="sheet sheet--inside">
  <article class="panel panel--soft">
    <div class="step">
      <span class="step__num">1.</span><span class="step__label">SCHRITT</span>
      <span class="step__icon"><svg width="20" height="20" viewBox="0 0 20 20"><circle cx="9" cy="6" r="3.5" fill="#2f2f2f"/><path d="M2 16c0-4 3-6 7-6s5 1 6 2" fill="#2f2f2f"/><circle cx="15" cy="14" r="3" fill="#2f2f2f" stroke="#f4b71c"/></svg></span>
    </div>
    <h2 class="heading" style="margin-top:14px">REGISTRIERUNG<br>UND ANMELDUNG</h2>
    <p class="justify">Wenn Sie Neukunde sind, legen Sie bitte zunächst ein neues Benutzerkonto auf unserem Online-Portal an:</p>
    <span class="url">https://kundenportal.testoval.se/de</span>
    <p class="justify">Anschließend können Sie die Radondetektoren registrieren. Vermerken Sie den Start der Messung (Datum und Uhrzeit), die Messorte (Raum und Etage) sowie die 9-stellige Seriennummer der Detektoren, die Sie auf der Verpackung oder auf der Unterseite der jeweiligen Detektoren finden.</p>
    <p class="justify" style="font-style:italic;margin-top:10px">Firmenkunden haben die Möglichkeit eine Excel-Datei als Hilfsmittel herunterzuladen, die Sie ausfüllen und dann wieder hochladen.</p>
    <div class="step" style="margin-top:20px">
      <span class="step__num">2.</span><span class="step__label">SCHRITT</span>
      <span class="step__icon"><svg width="20" height="20" viewBox="0 0 20 20"><path d="M10 18s-6-6-6-10a6 6 0 0 1 12 0c0 4-6 10-6 10z" fill="#2f2f2f"/><circle cx="10" cy="8" r="2.2" fill="#f4b71c"/></svg></span>
    </div>
    <h2 class="heading" style="margin-top:14px">PLATZIERUNG<br>DER DETEKTOREN</h2>
    <p class="justify">Bevor Sie die Detektoren der Verpackung entnehmen, überlegen Sie wo genau Sie die Radondetektoren platzieren wollen. Die Radonmessung beginnt, sobald Sie die radondichten Verpackungen öffnen. Beachten Sie bei der Platzierung zunächst die Auswahl der Räume und die Positionierung der Radondetektoren im Raum.</p>
  </article>

  <article class="panel panel--grey">
    <div class="note" style="margin-top:44px">
      <svg width="26" height="26" viewBox="0 0 26 26"><rect x="2" y="6" width="17" height="17" rx="3" fill="none" stroke="#2f2f2f" stroke-width="2"/><path d="M6 14l5 5 12-15" fill="none" stroke="#f4b71c" stroke-width="3"/></svg>
      <p>Für eine zuverlässige Radonmessung empfehlen wir wie folgt vorzugehen:</p>
    </div>
    <h2 class="heading" style="margin-top:18px">AUSWAHL DER RÄUME</h2>
    <div class="sub">
      <svg width="26" height="22" viewBox="0 0 26 22"><path d="M2 11L13 2l11 9" fill="none" stroke="#f4b71c" stroke-width="2.2"/><rect x="6" y="10" width="14" height="11" fill="#f4b71c"/><rect x="11" y="14" width="4" height="7" fill="#fff"/></svg>
      <h3>Einfamilienhäuser</h3>
    </div>
    <ul class="bullets">
      <li>Es sollten mindestens zwei Wohnräume und pro bewohnte Etage mindestens ein Wohnraum gemessen werden. Wählen Sie Räume aus, in denen Sie sich oft aufhalten (z.B. das Wohn- und Schlafzimmer). Vermeiden Sie aber Räume, in denen das Fenster mehrere Stunden am Tag oder in der Nacht geöffnet ist.</li>
      <li>Insofern Sie einen Keller haben, empfehlen wir alle Kellerräume zu messen, da hier meist das größte Risiko einer erhöhten Radonkonzentration erwartet wird.</li>
    </ul>
    <div class="sub" style="margin-top:16px">
      <svg width="26" height="30" viewBox="0 0 26 30"><path d="M3 9L13 2l10 7" fill="none" stroke="#f4b71c" stroke-width="2.2"/><rect x="6" y="8" width="14" height="21" fill="#f4b71c"/><g fill="#fff"><rect x="9" y="11" width="3" height="3"/><rect x="14" y="11" width="3" height="3"/><rect x="9" y="17" width="3" height="3"/><rect x="14" y="17" width="3" height="3"/><rect x="11" y="23" width="4" height="6"/></g></svg>
      <h3>Mehrfamilienhäuser, Wohnungen<br>und Wohnkomplexen</h3>
    </div>
    <ul class="bullets">
      <li>Alle Wohnungen mit direktem Bodenkontakt sowie mindestens eine Wohnung pro Etage sollten gemessen werden. Wählen Sie dabei Wohnungen, die an Aufzügen oder Luftschächten liegen.</li>
      <li>In größeren Wohnkomplexen sollten insgesamt mindestens 20 % aller Wohnungen in einem Gebäude gemessen werden.</li>
      <li>Es sollten mindestens zwei Wohnräume pro ausgewählte Wohnung gemessen werden. Wählen Sie Räume aus, in denen Sie sich oft aufhalten (z.B. das Wohn- und Schlafzimmer). Vermeiden Sie aber Räume, in denen das Fenster mehrere Stunden am Tag oder in der Nacht geöffnet ist.</li>
      <li>Selbst bei einer Einzimmerwohnung sollten Sie zwei Detektoren aufstellen.</li>
    </ul>
  </article>

  <article class="panel">
    <div class="strip-art" role="img" aria-label="Illustration: Ausschnitt der Stadtsilhouette in Gelbtönen"></div>
    <div class="sub" style="margin-top:16px">
      <svg width="24" height="28" viewBox="0 0 24 28"><rect x="2" y="2" width="20" height="25" fill="none" stroke="#f4b71c" stroke-width="2"/><g fill="#f4b71c"><rect x="6" y="6" width="4" height="4"/><rect x="14" y="6" width="4" height="4"/><rect x="6" y="13" width="4" height="4"/><rect x="14" y="13" width="4" height="4"/><rect x="6" y="20" width="4" height="4"/><rect x="14" y="20" width="4" height="4"/></g></svg>
      <h3>Arbeitsplätze und öffentliche Gebäude</h3>
    </div>
    <ul class="bullets">
      <li>Wählen Sie Räume, die regelmäßig mehr als vier Stunden pro Tag genutzt werden.</li>
      <li>Messen Sie alle unterirdischen Räumlichkeiten, da hier meist das größte Risiko einer erhöhten Radonkonzentration erwartet wird.</li>
      <li>Messen Sie alle Räume im Erdgeschoß. Für größere Räumlichkeiten empfehlen wir einen Detektor pro 200 m².</li>
      <li>In den oberen Etagen sollten Sie mit mindestens zwei Detektoren, sowie mindestens einem Detektor pro 200 m² messen.</li>
      <li>Falls Ihr Arbeitsplatz in einem Radon-Vorsorgegebiet liegt und somit der Messpflicht unterliegt, muss die Messdauer von 12 Monaten eingehalten werden.</li>
    </ul>
    <div class="sub" style="margin-top:16px">
      <svg width="30" height="22" viewBox="0 0 30 22"><rect x="2" y="2" width="26" height="18" fill="none" stroke="#f4b71c" stroke-width="2"/><rect x="6" y="6" width="18" height="10" fill="none" stroke="#f4b71c" stroke-width="1.4"/></svg>
      <h3>Platzierung der Detektoren im Raum</h3>
    </div>
    <ul class="bullets">
      <li>Platzieren Sie die Detektoren in einem Mindestabstand von 20 cm zu Wänden, 50 cm zu Abluftsventilen, sowie 1,50 m zu Fenstern, Außentüren, Zuluftsventilen und Heizkörpern.</li>
      <li>Stellen Sie die Detektoren nicht auf dem Boden, an starken Wärmequellen oder Luftströmen auf. Vermeiden Sie auch Räume mit hoher Luftfeuchtigkeit, wie zum Beispiel das Badezimmer.</li>
      <li>Die Detektoren können entweder stehend (auf einem Tisch, im Regal oder einer Schrankwand) oder hängend mitten im Raum (z.B. von einer Lampe) platziert werden.</li>
      <li>Stellen Sie die Detektoren während der gesamten Messdauer nicht um.</li>
      <li>Versuchen Sie nicht das Gehäuse der Detektoren zu öffnen und platzieren Sie diese immer außer Reichweite von Kindern.</li>
    </ul>
  </article>
</section>

</body>
</html>
```